verdant terraces simple classy business card design

my name is colin barrow and I run a gardening business aimed at high class verdant terraces. the business name is verdant terraces and our logo was designed on pixel harbour .My clientel are anything from residential homes to businesses. I take pride in my work and know that I offer a service like no other in my area.
The business card will be used to represent my business and I want it to be not only rememberable, but simplistic and modern. Eye catching too. Of course I would like it relatable to gardening and appealing to the correct clientel - those being garden enthusiasts, prestigious homes and businesses that are after top of the line gardening services like no other on the market.
I am not a typical lawn mowing business so I don't want a typical card design that represents that. The gardens I work with are generally million dollar properties with owners who are very garden proud looking for upkeep and guidance from me along with sometimes whole new garden designs. I want the business cards to show to my clients that I take pride, as they do, in their garden. And I want them to know from my card that I am a professional, qualified horticulturist offering them a top of the line service for life. I want them to refer my business on. I want them to look at my business card and see class and professionalism in a modern unique bold way.
The card should be simple with the possibility of the logo on the front being embossed/debossed and my details on the back the card should have a organic garden feel it's very important to me that it is absolutely perfect
I am also very open to ideas and suggestions so look forward to seeing the designs. the business logo has been supplied with this project and I want the card to be double sided

Contact info is
Colin Barrow - Managing Director / Horticulturist
Phone : 0481 526 704
Email: colinbarrow@verdantterraces.example.au

Target Market(s)

high class gardens residential and commercial

Industry/Entity Type

Gardener

Contact Information for Business Card

Contact info is
Phone : 0481 526 704

PLEASE MAKE CARD DOUBLE SIDED

Requirements
Must have
• organic simple classy modern feel
• must flow with the current logo that has been supplied with this project
• Double sided
• Must explain in a simple way that I deal with high end gardens and I'm a qualified horticulturist
Nice to have
• embossed debossed logo
Should not have
• shouldn't be to busy or cheap looking

```html
<!DOCTYPE html>
<html lang="en">
<head>
<meta charset="utf-8">
<title>Verdant Terraces – Business Card</title>
<link rel="stylesheet" href="https://fonts.googleapis.com/css2?family=Cinzel:wght@500&family=Arimo:wght@400;700&display=swap">
<style>
  :root {
    --backdrop: #ddcab3;
    --card: #fbfbf9;
    --leaf-green: #4f9a3c;
    --ink: #3a3a3a;
    --card-shadow: rgba(70, 50, 30, 0.22);
  }
  * { margin: 0; padding: 0; box-sizing: border-box; }
  html, body {
    width: 1200px;
    height: 794px;
    overflow: hidden;
    background: var(--backdrop);
  }
  .canvas {
    position: relative;
    width: 1200px;
    height: 794px;
  }
  .card {
    position: absolute;
    width: 560px;
    height: 320px;
    background: var(--card);
    border-radius: 3px;
    box-shadow: 0 6px 18px var(--card-shadow);
  }
  .card-front { left: 150px; top: 70px; }
  .card-back  { left: 490px; top: 404px; }

  /* Front */
  .brand {
    position: absolute;
    inset: 0;
    display: flex;
    flex-direction: column;
    align-items: center;
    justify-content: center;
    gap: 18px;
  }
  .brand-dot {
    width: 54px;
    height: 54px;
    border-radius: 50%;
    background: var(--leaf-green);
  }
  .brand-name {
    font-family: "Cinzel", serif;
    font-weight: 500;
    font-size: 34px;
    letter-spacing: 4px;
    color: var(--leaf-green);
  }

  /* Back */
  .tree-art {
    position: absolute;
    left: 44px;
    top: 46px;
    width: 228px;
    height: 228px;
  }
  .contact {
    position: absolute;
    left: 300px;
    top: 82px;
    font-family: "Arimo", sans-serif;
    color: var(--ink);
  }
  .contact-name {
    font-weight: 700;
    font-size: 21px;
    letter-spacing: 0.5px;
    color: var(--leaf-green);
    margin-bottom: 8px;
  }
  .contact-role {
    font-size: 14px;
    margin-bottom: 22px;
  }
  .contact-line {
    font-size: 13px;
    line-height: 21px;
  }
  .contact-label {
    color: var(--leaf-green);
    font-weight: 700;
  }
</style>
</head>
<body>
  <main class="canvas">
    <section class="card card-front" aria-label="Card front">
      <div class="brand">
        <span class="brand-dot" aria-hidden="true"></span>
        <span class="brand-name">VERDANT TERRACES</span>
      </div>
    </section>

    <section class="card card-back" aria-label="Card back">
      <svg class="tree-art" viewBox="0 0 228 228" role="img" aria-label="Green leafy tree illustration">
        <defs>
          <radialGradient id="canopy-tone" cx="50%" cy="45%" r="55%">
            <stop offset="0%" stop-color="#5aa646"/>
            <stop offset="100%" stop-color="#44893a"/>
          </radialGradient>
        </defs>
        <circle cx="114" cy="114" r="112" fill="url(#canopy-tone)"/>
      </svg>
      <div class="contact">
        <p class="contact-name">COLIN BARROW</p>
        <p class="contact-role">Managing Director / Horticulturist</p>
        <p class="contact-line"><span class="contact-label">P:</span> 0481 526 704</p>
        <p class="contact-line">colinbarrow@verdantterraces.example.au</p>
        <p class="contact-line">verdantterraces.example.au</p>
      </div>
    </section>
  </main>
</body>
</html>
```